Velvet Loom (E-commerce) Website for Embroidery shop

Briefing:

Velvet Loom is an online personalized embroidery shop targeting mainly three customer segments:
1) lovers and marring couples
2) close friends wishing to give unique gifts
3) moms with new born baby personalized gifts

These customers are being served through our three major business lines:
1) Bathrobes and towels with personalized embroidery
2) Embroidered pillows and cushions
3) baby gifts with costumed baby sets stitched

Requirements:

The business has been recently established with moderate variety of products introduced so far. The website must consists of four major pages; a home page and three pages for every single business line. All images necessary for the web design are shareable upon request for copyright reasons if necessary. Please post a few products in each page to make it easy for the employee to use as benchmarks to upload other products.

The website also should contain all items and buttons exist in any e-commerce website such as:

1- social links:
a. (Major) Instagram: https://www.instagram.com/velvet.loom.studio/
b. Twitter: https://twitter.com/Velvet_Loom_
c. Facebook: https://www.facebook.com/Velvet.loom.studio/
d. Snapchat: coming soon

2- Help:
a. Delivery & Returns (inside KSA)
I. Delivery:
- Rush: within 3 business days (SAR 90)
- Express: within 5 business days (SAR 65)
- Standard: 7-10 business days ( SAR 35)
II. Returns: We guarantee you will love our product. But if you don't like it, send it back to us within two days from delivery and we will donate it to a charity and return your money subject to our terms and conditions.

b. Contact:
- Email: Velvet.loom.studio@plumemail.net
- (Mobile) Whats-app: +966 54 312 9067 (for quick response)

d. Warranty:
for only SAR 20 per product, we will give you a lifetime warranty over our German stitches

3- Payment options:
bank transfer, visa, MasterCard and PayPal

Remarks:

- This website is mainly aimed at customers in Saudi Arabia where some contents may not appeal to people from such country and results in your participation being excluded from the contest.

- You are the expert and if I am a webdesigner, I would have not posted this contest, so please use your our own judgment and creativity to come up with the best experience possible.

- Use our Instagram account as your first reference to understand our business as it is our major channel that has been used to reach our customers. Please don't use the pictures with poor quality as we will be replacing them with other images with better quality.

- We intend to have this website bilingual (i.e English and Arabic), so if you can translate it into Arabic, then we will pay you an extra $100 in addition to the contest price.

- If in doubt, please feel free to ask any question and suggestions are always encouraged and warm welcomed.

- If you succeed in this contest, you will be chosen as our ultimate Web designer. That means you will have a long relationship providing services to our customers under one of our businesses that aims at preparing start-up companies establishing their business.

Target Market(s)

1) lovers and marrying couples

Industry/Entity Type

Embroidery

Number of Pages Required

4 page

Font styles to use
Serif
Script

Colors

Designer to choose colors to be used in the design.

Requirements
Must have
• Requirements:
• The business has been recently established with moderate variety of products introduced so far. The website must consists of four major pages; a home page and three pages for every single business line. All images necessary for the web design are shareable upon request for copyright reasons if necessary. Please post a few products in each page to make it easy for the employee to use as benchmarks to upload other products.
• The Website must be also mobile use friendly!!!
• The website also should contain all items and buttons exist in any e-commerce website such as:
• 1- social links:
• a. (Major) Instagram: https://www.instagram.com/velvet.loom.studio/
• b. Twitter: https://twitter.com/Velvet_Loom_
• c. Facebook: https://www.facebook.com/Velvet.loom.studio/
• d. Snapchat: coming soon
• 2- Help:
• a. Delivery & Returns (inside KSA)
• I. Delivery:
• - Rush: within 3 business days (SAR 90)
• - Express: within 5 business days (SAR 65)
• - Standard: 7-10 business days ( SAR 35)
• II. Returns: We guarantee you will love our product. But if you don't like it, send it back to us within two days from delivery and we will donate it to a charity and return your money subject to our terms and conditions.
• b. Contact:
• - Email: Velvet.loom.studio@plumemail.net
• - (Mobile) Whats-app: +966 54 312 9067 (for quick response)
• d. Warranty:
• for only SAR 20 per product, we will give you a lifetime warranty over our German stitches
• 3- Payment options:
• bank transfer, visa, MasterCard and PayPal
• Note: You will be responsible to upload the design to the website fully and ensure its integration and functionality.

```html
<!DOCTYPE html>
<html lang="en">
<head>
<meta charset="utf-8">
<title>Velvet Loom — Embroidery Shop</title>
<link rel="stylesheet" href="https://fonts.googleapis.com/css2?family=Montserrat:wght@400;500;600&display=swap">
<style>
:root{
  --gold:#b8913f;
  --text:#6e6e6e;
  --dark:#4a4a4a;
  --line:#dcdcdc;
  --footer:#f1f1f1;
  --white:#ffffff;
}
*{box-sizing:border-box;margin:0;padding:0}
html,body{width:1200px;height:2347px;overflow:hidden}
body{font-family:'Montserrat',sans-serif;color:var(--text);background:var(--white);position:relative}
a{color:inherit;text-decoration:none}

/* header */
.site-header{position:absolute;left:0;top:0;width:1200px;height:113px;background:var(--white)}
.brand{position:absolute;left:133px;top:36px;font-size:30px;font-weight:500;color:var(--gold);letter-spacing:.5px}
.top-links{position:absolute;right:133px;top:20px;display:flex;align-items:center;font-size:11px;text-transform:uppercase;color:var(--dark)}
.top-links .sep{margin:0 12px}
.btn-app{margin-left:18px;background:var(--gold);color:var(--white);border-radius:18px;width:113px;height:32px;display:flex;align-items:center;justify-content:center;font-weight:600;font-size:10.5px}
.lang{margin-left:26px;font-size:11px}
.lang .on{color:var(--gold)}
.main-nav{position:absolute;left:482px;top:80px;display:flex;font-size:11px;text-transform:uppercase;color:var(--dark)}
.main-nav a{margin-right:38px}
.main-nav a.active{color:var(--gold)}
.cart{position:absolute;right:133px;top:80px;font-size:11px;text-transform:uppercase;color:var(--dark);display:flex;align-items:center;gap:5px}

/* hero */
.hero{position:absolute;left:0;top:113px;width:1200px;height:430px;
  background:
    linear-gradient(rgba(40,38,36,.35),rgba(40,38,36,.35)),
    radial-gradient(ellipse 520px 300px at 560px 170px,#d9d6d1 0%,#a8a49f 45%,transparent 75%),
    radial-gradient(ellipse 300px 260px at 1080px 120px,#8c8782 0%,transparent 70%),
    linear-gradient(160deg,#6f6b67 0%,#58544f 55%,#3f3c39 100%)}
.hero h1{position:absolute;left:0;width:1200px;top:108px;text-align:center;color:var(--white);font-size:47px;font-weight:500;letter-spacing:1px}
.hero p{position:absolute;left:0;width:1200px;top:188px;text-align:center;color:var(--white);font-size:20px}
.btn-shop{position:absolute;left:529px;top:247px;width:141px;height:40px;border-radius:20px;background:var(--gold);color:var(--white);font-size:11px;font-weight:600;display:flex;align-items:center;justify-content:center}
.dots{position:absolute;left:580px;top:386px;display:flex;gap:5px}
.dots span{width:10px;height:10px;border-radius:50%;border:1.5px solid var(--white)}
.dots span.on{background:var(--white)}

/* categories */
.category{position:absolute;top:574px;width:301px;height:199px;display:flex;align-items:flex-end;justify-content:center;padding-bottom:17px;text-align:center;color:var(--white);font-size:19px;line-height:24px}
.cat-couples{left:133px;background:
  linear-gradient(rgba(60,55,52,.35),rgba(60,55,52,.35)),
  radial-gradient(ellipse 120px 110px at 70px 70px,#e6d7b8 0%,transparent 70%),
  radial-gradient(ellipse 120px 120px at 240px 60px,#a83a3e 0%,transparent 72%),
  linear-gradient(135deg,#b19373,#7d5d55)}
.cat-friends{left:450px;background:
  linear-gradient(rgba(60,55,52,.35),rgba(60,55,52,.35)),
  radial-gradient(ellipse 170px 130px at 150px 80px,#d7cfc6 0%,transparent 75%),
  linear-gradient(135deg,#9b9390,#5c5654)}
.cat-moms{left:766px;background:
  linear-gradient(rgba(70,66,76,.3),rgba(70,66,76,.3)),
  radial-gradient(ellipse 160px 120px at 150px 70px,#d8d6de 0%,transparent 75%),
  linear-gradient(135deg,#aaa7b3,#7f7b88)}

/* section titles */
.section-title{position:absolute;left:0;width:1200px;text-align:center;font-size:28px;font-weight:500;color:var(--text);text-transform:uppercase}

/* products */
.product{position:absolute;top:907px;width:219px;height:312px;border:1px solid var(--line);background:var(--white)}
.product .thumb{height:148px}
.product .name{position:absolute;top:165px;width:100%;text-align:center;font-size:19px;color:var(--text)}
.product .price{position:absolute;top:199px;width:100%;text-align:center;font-size:25px;font-weight:600;color:var(--gold)}
.btn-cart{position:absolute;left:53px;top:248px;width:113px;height:38px;border-radius:19px;border:1px solid #9a9a9a;font-size:10px;color:var(--dark);display:flex;align-items:center;justify-content:center;text-transform:uppercase}
.btn-cart.filled{background:var(--gold);border-color:var(--gold);color:var(--white);font-weight:600}
.p1{left:133px}.p1 .thumb{background:
  radial-gradient(ellipse 70px 60px at 60px 50px,#cfe4f0 0%,transparent 70%),
  radial-gradient(ellipse 90px 70px at 170px 90px,#7f9fb5 0%,transparent 70%),
  linear-gradient(135deg,#6a6c6f,#45474b)}
.p2{left:372px}.p2 .thumb{background:
  radial-gradient(ellipse 80px 50px at 60px 40px,#8a6a9c 0%,transparent 75%),
  radial-gradient(ellipse 110px 60px at 130px 110px,#f3f1f3 0%,transparent 75%),
  linear-gradient(135deg,#cfc8d4,#a79bb0)}
.p3{left:612px}.p3 .thumb{background:
  radial-gradient(ellipse 80px 65px at 100px 75px,#ffffff 0%,#f1eef0 55%,transparent 80%),
  radial-gradient(ellipse 40px 40px at 200px 130px,#a13038 0%,transparent 75%),
  linear-gradient(135deg,#d9d6d8,#9f9a9d)}
.p4{left:851px}.p4 .thumb{background:
  radial-gradient(ellipse 90px 80px at 60px 90px,#ef8e82 0%,transparent 75%),
  radial-gradient(ellipse 80px 70px at 170px 80px,#ece8e4 0%,transparent 75%),
  linear-gradient(135deg,#e09a8d,#c2a99b)}

/* testimonials */
.testimonials{position:absolute;left:0;top:1281px;width:1200px;height:376px;background:
  linear-gradient(rgba(60,45,60,.35),rgba(60,45,60,.35)),
  radial-gradient(ellipse 360px 260px at 260px 160px,#9a7d99 0%,transparent 70%),
  radial-gradient(ellipse 420px 300px at 900px 200px,#cfc9cf 0%,transparent 70%),
  linear-gradient(120deg,#6e5670 0%,#8c7f8a 55%,#6a586c 100%)}
.testimonials h2{position:absolute;left:0;width:1200px;top:56px;text-align:center;color:var(--white);font-size:29px;font-weight:500}
.quote{position:absolute;top:136px;width:440px;color:var(--white)}
.quote .avatar{position:absolute;left:0;top:0;width:100px;height:100px;border-radius:50%;border:3px solid var(--white);background:radial-gradient(circle at 50% 35%,#e3e0dc 0%,#c9a892 45%,#6f7b86 100%)}
.quote p{position:absolute;left:133px;top:12px;font-size:12.5px;font-weight:500;line-height:24px;white-space:nowrap}
.quote .who{position:absolute;left:133px;top:136px;font-size:13px;font-weight:500}
.q1{left:133px}
.q2{left:621px}

/* instagram */
.insta{position:absolute;top:1768px;width:219px;height:202px}
.i1{left:133px;background:
  radial-gradient(ellipse 110px 70px at 100px 45px,#f3a9cf 0%,transparent 75%),
  radial-gradient(ellipse 120px 70px at 110px 130px,#f7f4f1 0%,transparent 75%),
  linear-gradient(135deg,#e7a4c4,#c9b7a8)}
.i2{left:372px;background:
  radial-gradient(ellipse 110px 60px at 110px 60px,#a8404f 0%,transparent 75%),
  radial-gradient(ellipse 60px 40px at 110px 140px,#efe9ea 0%,transparent 75%),
  linear-gradient(135deg,#6f1a27,#8e2a3a)}
.i3{left:612px;background:
  radial-gradient(ellipse 130px 100px at 100px 120px,#f3f1f1 0%,#dcd8d9 55%,transparent 80%),
  linear-gradient(135deg,#7a1f44,#4e1530)}
.i4{left:851px;background:
  radial-gradient(ellipse 60px 70px at 110px 100px,#2f6f88 0%,transparent 70%),
  radial-gradient(ellipse 140px 120px at 110px 100px,#f2f2f2 0%,transparent 80%),
  linear-gradient(135deg,#e2e2e2,#a8a8a8)}

/* footer */
.site-footer{position:absolute;left:0;top:2024px;width:1200px;height:323px;background:var(--footer)}
.footer-brand{position:absolute;left:133px;top:60px;font-size:30px;font-weight:500;color:var(--gold)}
.contact{position:absolute;left:133px;top:160px;font-size:11.5px;line-height:23px;color:var(--text)}
.f-col{position:absolute;top:60px}
.f-col h3{font-size:18px;font-weight:500;color:var(--text);text-transform:uppercase;margin-bottom:14px}
.f-col li{list-style:none;font-size:11.5px;line-height:23.5px}
.col-links{left:433px}
.col-account{left:644px}
.col-news{left:798px}
.newsletter{position:absolute;left:5px;top:47px;display:flex}
.newsletter .field{width:183px;height:31px;border:1px solid var(--line);background:var(--white);font-size:10.5px;color:var(--text);padding-left:10px;display:flex;align-items:center}
.newsletter .subscribe{width:79px;height:31px;background:var(--gold);color:var(--white);font-size:10px;font-weight:600;display:flex;align-items:center;justify-content:center}
.payments{position:absolute;left:181px;top:115px;display:flex;gap:4px}
.payments span{width:26px;height:17px;border-radius:2px;border:1px solid rgba(0,0,0,.15)}
.pay-a{background:linear-gradient(#f0a24a,#d97f24)}
.pay-b{background:linear-gradient(#3c86cc,#24619f)}
.pay-c{background:linear-gradient(#e8eef3,#c9d4de)}
.copyright{position:absolute;left:0;width:1200px;top:274px;text-align:center;font-size:11px;color:var(--text)}
</style>
</head>
<body>

<header class="site-header">
  <a class="brand" href="#">Velvet Loom</a>
  <div class="top-links">
    <a href="#">Sign up</a><span class="sep">|</span><a href="#">Log in</a>
    <a class="btn-app" href="#">GET APP</a>
    <span class="lang"><span class="on">EN</span> / AR</span>
  </div>
  <nav class="main-nav">
    <a class="active" href="#">Home</a>
    <a href="#">About us</a>
    <a href="#">Products</a>
    <a href="#">Blog</a>
    <a href="#">Contact us</a>
  </nav>
  <div class="cart">Your cart
    <svg width="13" height="11" viewBox="0 0 13 11"><path d="M0 1h2.5l1.7 6h6.6L12.5 2.5H3.3" fill="none" stroke="#b8913f" stroke-width="1.5"/><circle cx="5" cy="9.5" r="1.2" fill="#b8913f"/><circle cx="10" cy="9.5" r="1.2" fill="#b8913f"/></svg>
    0 items</div>
</header>

<section class="hero" role="img" aria-label="Embroidered white pillow with a personalised message">
  <h1>EMBROIDERY SHOP</h1>
  <p>Embroider your unforgettable memories with gold so they last forever...</p>
  <a class="btn-shop" href="#">SHOP NOW</a>
  <div class="dots"><span class="on"></span><span></span><span></span></div>
</section>

<a class="category cat-couples" href="#" role="img" aria-label="Embroidered bathrobes with couple names">Lovers and Marring<br>Couples</a>
<a class="category cat-friends" href="#" role="img" aria-label="Embroidered calendar pillow gift">Close friends Wishing to<br>Give unique gifts</a>
<a class="category cat-moms" href="#" role="img" aria-label="Personalised baby blanket with name">Moms with New born<br>Baby personalized gifts</a>

<h2 class="section-title" style="top:838px">Featured Products</h2>

<div class="product p1"><div class="thumb" role="img" aria-label="Grey towel embroidered with a name and blue ribbon"></div><div class="name">Velvet Loom</div><div class="price">$50.00</div><a class="btn-cart filled" href="#">Add to cart</a></div>
<div class="product p2"><div class="thumb" role="img" aria-label="Lavender towel set embroidered with a name"></div><div class="name">Velvet Loom</div><div class="price">$50.00</div><a class="btn-cart" href="#">Add to cart</a></div>
<div class="product p3"><div class="thumb" role="img" aria-label="White calendar pillow with embroidered date"></div><div class="name">Velvet Loom</div><div class="price">$50.00</div><a class="btn-cart" href="#">Add to cart</a></div>
<div class="product p4"><div class="thumb" role="img" aria-label="Coral and white towels embroidered with names"></div><div class="name">Velvet Loom</div><div class="price">$50.00</div><a class="btn-cart" href="#">Add to cart</a></div>

<section class="testimonials" role="img" aria-label="Purple and white embroidered bathrobes with names">
  <h2>Testimonials</h2>
  <div class="quote q1">
    <div class="avatar" role="img" aria-label="Customer portrait"></div>
    <p>Nemo enim ipsam voluptatem quia voluptas sit<br>aspernatur aut odit aut fugit, sed quia consequun-<br>tur magni dolores eos qui ratione voluptatem<br>sequi nesciunt.</p>
    <div class="who">- Rakan -</div>
  </div>
  <div class="quote q2">
    <div class="avatar" role="img" aria-label="Customer portrait"></div>
    <p>Nemo enim ipsam voluptatem quia voluptas sit<br>aspernatur aut odit aut fugit, sed quia consequun-<br>tur magni dolores eos qui ratione voluptatem<br>sequi nesciunt.</p>
    <div class="who">- Rakan -</div>
  </div>
</section>

<h2 class="section-title" style="top:1700px">Instagram</h2>
<div class="insta i1" role="img" aria-label="Pink baby gift set with embroidered towel"></div>
<div class="insta i2" role="img" aria-label="Burgundy towel embroidered with a name"></div>
<div class="insta i3" role="img" aria-label="White towel embroidered with an initial"></div>
<div class="insta i4" role="img" aria-label="White towel embroidered with a blue initial"></div>

<footer class="site-footer">
  <div class="footer-brand">Velvet Loom</div>
  <div class="contact">Velvet.loom.studio@plumemail.net<br>+966 54 312 9067</div>
  <div class="f-col col-links"><h3>Quick links</h3><ul><li>Home</li><li>About us</li><li>Products</li><li>Blog</li><li>Contact us</li></ul></div>
  <div class="f-col col-account"><h3>Account</h3><ul><li>Shipping</li><li>Order</li><li>Login</li><li>Signup</li></ul></div>
  <div class="f-col col-news"><h3>Newsletter</h3>
    <div class="newsletter"><div class="field">Enter your mail id</div><div class="subscribe">SUBSCRIBE</div></div>
    <div class="payments" aria-label="Accepted payment methods"><span class="pay-a"></span><span class="pay-b"></span><span class="pay-c"></span></div>
  </div>
  <div class="copyright">2017 © Velvet Loom. All Right Reserved.</div>
</footer>

</body>
</html>
```